We would like to have one website and the similar (or the same) Facebook site.
We need only the first website without sub-pages and menus. We are preparing a new product for the market. On the page should be the logo, company data, few pictures and the text about our product.
The company color is red.
Company data are Korvelt GmbH, CH-4417 Ermendorf, Switzerland, media@korvelt.example, www.korvelt.example.
Text for the page:
"We are Swiss engineers with many years of experience in ultra-precision electronics.
We develop the TidoBand, a smartwatch that can save lives. It is designed for elderly people who live alone and want to maintain their independence longer, without fear.
Our TidoBand will be available at 4th quarter of 2018."

```html
<!DOCTYPE html>
<html lang="en">
<head>
<meta charset="utf-8">
<title>Korvelt GmbH – TidoBand</title>
<link href="https://fonts.googleapis.com/css2?family=Lato:ital,wght@0,400;0,700;0,900;1,400&display=swap" rel="stylesheet">
<style>
:root{
  --red:#e0101f;
  --ink:#1d1d1d;
  --text:#333;
  --muted:#555;
  --grey-band:#eeeeee;
  --footer:#f2f2f2;
  --white:#fff;
}
*{box-sizing:border-box;margin:0;padding:0}
html,body{width:1200px;height:2866px;overflow:hidden;background:var(--white)}
body{font-family:'Lato',sans-serif;color:var(--text);position:relative}
section,header,footer{position:absolute;left:0;width:1200px}

.site-header{top:0;height:100px;background:var(--white)}
.brand{position:absolute;left:75px;top:26px;display:flex;align-items:center;gap:10px;font-size:44px;font-weight:700;color:var(--red);line-height:1}
.brand-dot{width:16px;height:16px;border-radius:50%;background:var(--red)}
.header-tagline{position:absolute;right:75px;top:42px;font-size:15px;font-weight:700;color:var(--ink);letter-spacing:.3px}

.hero{top:100px;height:561px}
.hero-photo{position:absolute;inset:0;background:linear-gradient(100deg,#4e6a2c 0%,#7b8f4a 30%,#9a8062 55%,#c9b9a5 75%,#6f8140 100%)}
.hero-copy{position:absolute;left:75px;top:200px;color:var(--white)}
.hero-title{font-size:50px;font-weight:700;line-height:1.1}
.hero-sub{font-size:25px;font-weight:700;line-height:1.15;width:560px;margin-top:4px}
.hero-dots{position:absolute;left:75px;top:501px;display:flex;gap:8px}
.hero-dots span{width:10px;height:10px;border-radius:50%;background:var(--white)}
.hero-dots span.on{background:var(--red)}

.welcome{top:661px;height:333px;text-align:center}
.section-title{font-size:33px;font-weight:400;color:var(--ink);line-height:1.2}
.section-title em{font-style:normal;color:var(--red)}
.welcome .section-title{margin-top:50px}
.welcome p{width:1050px;margin:20px auto 0;font-size:15px;line-height:29px;color:var(--text)}
.btn-outline{display:inline-block;border:2px solid var(--red);color:var(--ink);font-size:15px;font-weight:700;background:transparent;text-align:center}
.welcome .btn-outline{position:absolute;left:524px;top:224px;width:152px;height:50px;padding-top:14px}

.what{top:994px;height:412px}
.what-photo{position:absolute;inset:0;background:linear-gradient(90deg,#b5b0a3 0%,#cfcabd 45%,#d8d7c7 70%,#bcc1a8 100%)}
.what-product{position:absolute;left:130px;top:40px;width:450px;height:330px;border-radius:40px;background:linear-gradient(135deg,#2a2a2a,#111)}
.what-copy{position:absolute;left:625px;top:75px;width:490px}
.what-copy p{margin-top:14px;font-size:15px;line-height:29px;color:var(--text)}
.what-copy .btn-outline{margin-top:22px;width:152px;height:50px;padding-top:14px}

.features{top:1406px;height:467px}
.features .section-title{position:absolute;left:75px;top:56px}
.feature{position:absolute;left:75px;width:570px;display:flex}
.feature-icon{width:90px;flex:none;padding-top:10px;padding-left:13px}
.feature h3{font-size:19px;font-weight:700;color:var(--red);line-height:1.2}
.feature p{font-size:15px;line-height:23px;margin-top:6px;color:var(--text);width:480px}
.features-product{position:absolute;left:716px;top:65px;width:316px;height:335px;border-radius:50px;background:linear-gradient(135deg,#3a3a3a,#0f0f0f)}

.reviews{top:1873px;height:395px;background:var(--grey-band)}
.reviews .section-title{text-align:center;margin-top:42px}
.review{position:absolute;top:105px;width:505px}
.review blockquote{font-style:italic;font-size:14.5px;line-height:29px;color:var(--text);height:116px}
.reviewer{display:flex;align-items:center;margin-top:28px}
.avatar{width:88px;height:88px;border-radius:50%;background:linear-gradient(135deg,#c9a98a,#8d7a6a)}
.reviewer-name{margin-left:20px}
.reviewer-name strong{display:block;font-size:18px;color:var(--red)}
.reviewer-name span{font-style:italic;font-size:15px;color:var(--text)}

.buy{top:2268px;height:436px}
.buy-product{position:absolute;left:124px;top:54px;width:449px;height:334px;border-radius:46px;background:linear-gradient(135deg,#2f2f2f,#0e0e0e)}
.buy-copy{position:absolute;left:625px;top:88px;width:500px}
.buy-copy p{margin-top:14px;font-size:15px;line-height:29px;color:var(--text)}
.subscribe{position:absolute;left:625px;top:266px;display:flex;gap:16px}
.subscribe-input{width:334px;height:50px;border:2px solid #c9c9c9;font-size:14px;padding:15px 18px;color:var(--muted)}
.subscribe-btn{width:152px;height:50px;background:var(--red);color:var(--white);font-size:15px;font-weight:700;text-align:center;padding-top:16px;letter-spacing:.4px}

.site-footer{top:2704px;height:162px;background:var(--footer)}
.company-data{position:absolute;left:75px;top:56px;display:flex;gap:28px;font-size:13px;font-weight:700;color:var(--ink)}
.copyright{position:absolute;left:75px;top:86px;font-size:13px;color:var(--text)}
.social{position:absolute;right:75px;top:62px;display:flex;gap:22px}
.social span{width:22px;height:22px;border-radius:50%;background:#444}
</style>
</head>
<body>

<header class="site-header">
  <div class="brand"><span class="brand-dot"></span>Korvelt</div>
  <p class="header-tagline">Swiss ultra-precision electronics</p>
</header>

<section class="hero">
  <div class="hero-photo" role="img" aria-label="Smiling elderly couple embracing outdoors in a park, the man wearing a red smartwatch"></div>
  <div class="hero-copy">
    <h1 class="hero-title">TidoBand</h1>
    <p class="hero-sub">A smartwatch that can save lives. Available in the 4th quarter of 2018.</p>
  </div>
  <div class="hero-dots"><span class="on"></span><span></span><span></span><span></span></div>
</section>

<section class="welcome">
  <h2 class="section-title">Welcome to <em>Korvelt</em></h2>
  <p>We are Swiss engineers with many years of experience in ultra-precision electronics. We develop the TidoBand, a smartwatch that can save lives. It is designed for elderly people who live alone and want to maintain their independence longer, without fear. Our TidoBand will be available at 4th quarter of 2018.</p>
  <span class="btn-outline">READ MORE</span>
</section>

<section class="what">
  <div class="what-photo" role="img" aria-label="Faded photo of an elderly couple walking in a park"></div>
  <div class="what-product" role="img" aria-label="Two black TidoBand smartwatches, one showing the time and one an emergency call screen"></div>
  <div class="what-copy">
    <h2 class="section-title">What We Do</h2>
    <p>We develop the TidoBand, a smartwatch that can save lives. It is designed for elderly people who live alone and want to maintain their independence longer, without fear. Built by Swiss engineers with many years of experience in ultra-precision electronics.</p>
    <span class="btn-outline">READ MORE</span>
  </div>
</section>

<section class="features">
  <h2 class="section-title">Features</h2>
  <div class="feature" style="top:126px">
    <div class="feature-icon">
      <svg width="30" height="44" viewBox="0 0 30 44" aria-hidden="true"><rect x="8" y="0" width="14" height="44" rx="3" fill="#222"/><circle cx="15" cy="22" r="12" fill="#222"/><circle cx="15" cy="22" r="8" fill="#fff"/><path d="M15 17v5l3 3" stroke="#222" stroke-width="2" fill="none"/></svg>
    </div>
    <div><h3>Develop For Elderly People</h3><p>Designed for elderly people who live alone and want to keep their independence longer, without fear.</p></div>
  </div>
  <div class="feature" style="top:235px">
    <div class="feature-icon">
      <svg width="34" height="34" viewBox="0 0 34 34" aria-hidden="true"><circle cx="17" cy="17" r="14" fill="none" stroke="#222" stroke-width="6"/><circle cx="17" cy="17" r="14" fill="none" stroke="#fff" stroke-width="6" stroke-dasharray="8 14" stroke-dashoffset="4"/></svg>
    </div>
    <div><h3>Help to Save Lives</h3><p>A smartwatch that can save lives: one touch asks for help whenever its wearer needs it.</p></div>
  </div>
  <div class="feature" style="top:344px">
    <div class="feature-icon">
      <svg width="34" height="32" viewBox="0 0 34 32" aria-hidden="true"><rect x="0" y="13" width="8" height="18" fill="#222"/><path d="M10 13 L17 2 Q21 2 20 8 L19 12 H30 Q33 13 32 17 L29 29 Q28 31 25 31 H10 Z" fill="#222"/></svg>
    </div>
    <div><h3>Easy To Use</h3><p>Clear screen, large buttons and simple choices, built with Swiss ultra-precision electronics.</p></div>
  </div>
  <div class="features-product" role="img" aria-label="Black TidoBand smartwatch showing a help prompt with yes and no options"></div>
</section>

<section class="reviews">
  <h2 class="section-title">Reviews</h2>
  <div class="review" style="left:75px">
    <blockquote>“ My mother lives alone, and the TidoBand lets her stay independent while we know she can always call for help. It is simple to wear and simple to use, and it gives the whole family peace of mind every day..”</blockquote>
    <div class="reviewer"><div class="avatar" role="img" aria-label="Reviewer portrait"></div><div class="reviewer-name"><strong>Name Heading</strong><span>City</span></div></div>
  </div>
  <div class="review" style="left:615px">
    <blockquote>“ I wanted to keep living in my own home without fear. With the TidoBand on my wrist I feel safe, and the large screen is easy to read. Swiss precision you can trust, made for people like us..”</blockquote>
    <div class="reviewer"><div class="avatar" role="img" aria-label="Reviewer portrait"></div><div class="reviewer-name"><strong>Name Heading</strong><span>City</span></div></div>
  </div>
</section>

<section class="buy">
  <div class="buy-product" role="img" aria-label="Two black TidoBand smartwatches, one showing the time and one an emergency call screen"></div>
  <div class="buy-copy">
    <h2 class="section-title">Where to Buy</h2>
    <p>Our TidoBand will be available at 4th quarter of 2018. Leave your email address and we will tell you as soon as it can be ordered.</p>
  </div>
  <div class="subscribe">
    <div class="subscribe-input">Enter Email Address</div>
    <div class="subscribe-btn">SUBSCRIBE</div>
  </div>
</section>

<footer class="site-footer">
  <address class="company-data" style="font-style:normal"><span>Korvelt GmbH</span><span>CH-4417 Ermendorf, Switzerland</span><span>media@korvelt.example</span><span>www.korvelt.example</span></address>
  <p class="copyright">Copyright © 2018. Korvelt GmbH. All Rights Reserved</p>
  <div class="social" aria-label="Social media links"><span></span><span></span><span></span><span></span><span></span></div>
</footer>

</body>
</html>
```